Wren Arts Competition Event For Teenagers Needs Promo Graphics

I am in need of graphics for 2019 Prairie Wren Arts Showcase. It is a Wren Arts competition event for teenagers. I need graphics to make an 11x17 poster and a main title graphic that I can use for digital (social, 16x9 for screens, etc). Graphic should include the following 2 logos: the KM Rising Tide logo (this is who we are) and the "circles" logo is the logo of Wren Arts Showcase so that can be incorporated but is not mandatory and does not need to be in color. Tag line for Wren Arts is "Discover. Develop. Deploy." Again, this is optional. Looking for an artistic design - geometric shapes, bright colors, or something along those lines. Something that speaks to teenagers and especially creatives/Wren Arts types. Additionally, Post should include:
Harbor Lane Chapel
March 29-30
(registration & cost info may be added to the poster before design is finalized; still working on those details)

```html
<!DOCTYPE html>
<html lang="en">
<head>
<meta charset="utf-8">
<title>2019 Prairie Wren Arts Showcase – Title Graphics</title>
<link href="https://fonts.googleapis.com/css2?family=Saira+Semi+Condensed:wght@800&display=swap" rel="stylesheet">
<style>
  :root {
    --paper: #ffffff;
    --ink: #000000;
    --title-fill: #ffffff;
    --violet: #4b3a94;
    --plum: #8a3a8c;
    --magenta: #e8245f;
    --pink: #e85a9a;
    --cyan: #1aa6d8;
    --teal: #177f9c;
    --orange: #f47a20;
    --red: #ec1c24;
    --yellow: #fff200;
    --gold: #f7c52a;
  }
  html, body {
    margin: 0;
    width: 1200px;
    height: 902px;
    overflow: hidden;
    background: var(--paper);
  }
  .artboard {
    position: relative;
    width: 1200px;
    height: 902px;
  }
  .graphic {
    position: absolute;
    display: block;
    background: var(--ink);
  }
  .graphic--banner { left: 98px; top: 171px; width: 1006px; height: 125px; }
  .graphic--title  { left: 369px; top: 344px; width: 464px; height: 387px; }
  .headline {
    font-family: "Saira Semi Condensed", "Arial Narrow", sans-serif;
    font-weight: 800;
    fill: var(--title-fill);
    stroke-width: 5px;
    stroke-linejoin: round;
    paint-order: stroke fill;
  }
  .tagbox-text {
    font-family: "Saira Semi Condensed", "Arial Narrow", sans-serif;
    font-weight: 800;
    fill: var(--ink);
  }
</style>
</head>
<body>
<main class="artboard">

  <!-- Wide screen banner -->
  <svg class="graphic graphic--banner" viewBox="0 0 1006 125" aria-label="2019 Prairie Wren Arts Showcase banner">
    <defs>
      <linearGradient id="banner-shapes-left" x1="0" y1="0" x2="1" y2="1">
        <stop offset="0" stop-color="var(--cyan)"/>
        <stop offset="0.35" stop-color="var(--magenta)"/>
        <stop offset="0.65" stop-color="var(--orange)"/>
        <stop offset="1" stop-color="var(--violet)"/>
      </linearGradient>
      <linearGradient id="banner-shapes-right" x1="0" y1="1" x2="1" y2="0">
        <stop offset="0" stop-color="var(--magenta)"/>
        <stop offset="0.5" stop-color="var(--cyan)"/>
        <stop offset="1" stop-color="var(--gold)"/>
      </linearGradient>
      <linearGradient id="banner-outline" x1="0" y1="0" x2="1" y2="0">
        <stop offset="0" stop-color="var(--violet)"/>
        <stop offset="0.5" stop-color="var(--plum)"/>
        <stop offset="1" stop-color="var(--magenta)"/>
      </linearGradient>
      <linearGradient id="banner-tagbox" x1="0" y1="0" x2="1" y2="0">
        <stop offset="0" stop-color="var(--red)"/>
        <stop offset="0.5" stop-color="var(--orange)"/>
        <stop offset="1" stop-color="var(--yellow)"/>
      </linearGradient>
    </defs>
    <rect width="1006" height="125" fill="var(--ink)"/>
    <polygon role="img" aria-label="Colourful geometric triangle pattern" points="0,0 402,0 210,125 0,125" fill="url(#banner-shapes-left)"/>
    <polygon role="img" aria-label="Colourful geometric triangle pattern" points="1006,0 1006,125 814,125" fill="url(#banner-shapes-right)"/>
    <text class="headline" x="52" y="106" font-size="70" stroke="url(#banner-outline)" textLength="560" lengthAdjust="spacingAndGlyphs">2019 PRAIRIE</text>
    <rect x="706" y="46" width="252" height="35" fill="url(#banner-tagbox)"/>
    <text class="tagbox-text" x="712" y="73" font-size="26" textLength="240" lengthAdjust="spacingAndGlyphs">WREN ARTS SHOWCASE</text>
  </svg>

  <!-- Main title graphic -->
  <svg class="graphic graphic--title" viewBox="0 0 464 387" aria-label="2019 Prairie Wren Arts Showcase title graphic">
    <defs>
      <linearGradient id="title-shapes-left" x1="0" y1="0" x2="0.4" y2="1">
        <stop offset="0" stop-color="var(--teal)"/>
        <stop offset="0.3" stop-color="var(--orange)"/>
        <stop offset="0.6" stop-color="var(--pink)"/>
        <stop offset="1" stop-color="var(--gold)"/>
      </linearGradient>
      <linearGradient id="title-shapes-right" x1="0" y1="0" x2="0.3" y2="1">
        <stop offset="0" stop-color="var(--gold)"/>
        <stop offset="0.6" stop-color="var(--cyan)"/>
        <stop offset="1" stop-color="var(--pink)"/>
      </linearGradient>
      <linearGradient id="title-outline" x1="0" y1="0" x2="1" y2="0">
        <stop offset="0" stop-color="var(--violet)"/>
        <stop offset="0.5" stop-color="var(--plum)"/>
        <stop offset="1" stop-color="var(--magenta)"/>
      </linearGradient>
      <linearGradient id="title-tagbox" x1="0" y1="0" x2="1" y2="0">
        <stop offset="0" stop-color="var(--cyan)"/>
        <stop offset="0.5" stop-color="var(--plum)"/>
        <stop offset="1" stop-color="var(--magenta)"/>
      </linearGradient>
    </defs>
    <rect width="464" height="387" fill="var(--ink)"/>
    <polygon role="img" aria-label="Colourful geometric triangle pattern" points="0,0 55,0 200,230 125,387 0,387" fill="url(#title-shapes-left)"/>
    <polygon role="img" aria-label="Colourful geometric triangle pattern" points="351,0 464,0 464,176" fill="url(#title-shapes-right)"/>
    <text class="headline" x="31" y="144" font-size="70" stroke="url(#title-outline)" textLength="160" lengthAdjust="spacingAndGlyphs">2019</text>
    <text class="headline" x="31" y="236" font-size="104" stroke="url(#title-outline)" textLength="400" lengthAdjust="spacingAndGlyphs">PRAIRIE</text>
    <rect x="29" y="245" width="406" height="53" fill="url(#title-tagbox)"/>
    <text class="tagbox-text" x="39" y="286" font-size="40" textLength="386" lengthAdjust="spacingAndGlyphs">WREN ARTS SHOWCASE</text>
  </svg>

</main>
</body>
</html>
```